Travel Agency Website - Simple General

Need a 7 page simple design that is pretty repetitive. Need to be able to load quickly that is SEO optimized. Trying to give ideas on what they can do, be personal as we are local, but at the same time come across as professional and get information easily with little burden.

- Landing Page
- Brimwell Vacations Page
- Family Trips
- Road Trips from Texas
- Other Destinations
- About Us Page
- Contact Us Page

Target Market(s)

Families

Coding

Coded - Design and coding required

Number of Pages Required

5+ page

Colors

Designer to choose colors to be used in the design.

Requirements
Must have
• Like it to flow easily with our logo. Use that for colors, etc.

```html
<!DOCTYPE html>
<html lang="en">
<head>
<meta charset="utf-8">
<title>Meadowlark Roaming Travel Co. – Family Adventures</title>
<meta name="viewport" content="width=1200">
<link href="https://fonts.googleapis.com/css2?family=Outfit:wght@400;500;600;700&family=Poppins:wght@400;500;600&family=Great+Vibes&display=swap" rel="stylesheet">
<style>
:root{
  --teal:#1c5a68;
  --teal-dark:#123f4a;
  --footer:#0e2b31;
  --gold:#c4924a;
  --cream:#fdf9f3;
  --peach:#fdf0e1;
  --ink:#2a2f33;
  --muted:#5b6166;
  --line:#dcd5cb;
  --white:#ffffff;
}
*{margin:0;padding:0;box-sizing:border-box}
html,body{width:1200px;height:4890px;overflow:hidden}
body{background:var(--cream);font-family:"Poppins",sans-serif;color:var(--ink);position:relative}
.abs{position:absolute}
.script{font-family:"Great Vibes",cursive;color:var(--gold);font-weight:400;white-space:nowrap}
.heading{font-family:"Outfit",sans-serif;font-weight:600;color:var(--teal)}
.center{text-align:center;left:0;width:1200px}
.ph{position:absolute}

/* top bar */
.topbar{top:0;left:0;width:1200px;height:34px;background:var(--teal);color:#fff;font-size:12px;display:flex;justify-content:space-between;align-items:center;padding:0 142px}
.topbar span{display:flex;align-items:center;gap:8px}
.nav{top:34px;left:0;width:1200px;height:84px;background:var(--cream)}
.nav a{position:absolute;top:38px;font-size:12px;font-weight:500;color:var(--ink);text-decoration:none;letter-spacing:.3px}
.logo-badge{position:absolute;left:540px;top:4px;width:120px;height:100px;border-radius:50%;background:var(--white);border:2px solid var(--teal);display:flex;align-items:center;justify-content:center;text-align:center;font-family:"Outfit",sans-serif;font-weight:600;color:var(--teal);font-size:15px;line-height:1.15;z-index:3}

/* hero */
.hero{top:118px;left:0;width:1200px;height:562px;overflow:hidden}
.hero-photo{left:0;top:0;width:1200px;height:562px;background:linear-gradient(115deg,#4f7d4a 0%,#5d8aa0 35%,#9cc7d6 55%,#3f6b3e 75%,#6e6a5c 100%)}
.hero-cut{left:0;top:0}
.hero .script{left:142px;top:86px;font-size:48px;color:#fff}
.hero h1{left:142px;top:140px;font-family:"Outfit",sans-serif;font-weight:600;font-size:54px;line-height:56px;color:#fff}
.hero h1 em{font-family:"Great Vibes",cursive;font-style:normal;font-weight:400;font-size:60px}
.hero p{left:142px;top:256px;width:450px;font-size:12.5px;line-height:18px;color:#fff}
.btn{display:inline-flex;align-items:center;gap:14px;background:var(--gold);color:#fff;font-size:12px;font-weight:600;letter-spacing:.4px;border-radius:30px;padding:0 6px 0 18px;height:42px}
.btn .ring{width:32px;height:32px;border-radius:50%;border:2px solid #fff;background:#fff;display:flex;align-items:center;justify-content:center}
.hero .btn{position:absolute;left:142px;top:315px}

/* journey */
.card-photo{border-radius:10px}
.card-info{position:absolute;background:var(--white);border-radius:10px;box-shadow:0 6px 18px rgba(0,0,0,.08);padding:16px 20px}
.tag{display:inline-block;font-size:10px;color:#fff;padding:3px 11px;border-radius:10px;margin-bottom:6px}
.card-info h3{font-family:"Outfit",sans-serif;font-weight:500;font-size:24px;color:var(--ink);line-height:28px}
.card-info small{display:block;font-size:11px;color:var(--muted);letter-spacing:.3px;margin-top:4px}
.go{position:absolute;right:20px;top:40px;width:34px;height:34px;border-radius:50%;background:var(--teal);display:flex;align-items:center;justify-content:center}

/* banner */
.banner-card{left:646px;top:1815px;width:409px;height:269px;background:var(--white);border-radius:8px;padding:24px 22px;box-shadow:0 8px 24px rgba(0,0,0,.12)}
.banner-card .script{font-size:30px}
.banner-card h2{font-family:"Outfit",sans-serif;font-weight:600;color:var(--teal);font-size:34px;line-height:38px}
.banner-card p{font-size:12px;line-height:17px;margin-top:8px;color:var(--ink)}
.banner-card .btn{margin-top:18px}

/* about */
.about-text{left:142px;top:2240px;width:390px}
.about-text p{font-size:12.5px;line-height:22px;color:var(--ink);margin-top:8px}
.rule{width:96px;height:3px;background:var(--gold);margin-top:6px}

/* why */
.why{top:2759px;left:0;width:1200px;height:676px;background:var(--peach)}
.feat{position:absolute;font-size:12px;line-height:19px;color:var(--muted)}
.feat b{display:block;font-family:"Outfit",sans-serif;font-weight:600;font-size:15px;color:var(--ink)}
.feat.r{text-align:right}
.ico{position:absolute;width:64px;height:64px;border-radius:50%;background:var(--white);box-shadow:0 4px 14px rgba(0,0,0,.10);display:flex;align-items:center;justify-content:center}

/* form */
.field{position:absolute;background:var(--white);border:1px solid var(--line);border-radius:4px;font-size:11px;color:#9aa0a5;display:flex;align-items:center;gap:10px;padding:0 18px}
.field i{width:1px;height:18px;background:var(--line)}
.submit{left:293px;top:3891px;width:615px;height:52px;background:var(--gold);border-radius:4px;color:#fff;font-size:12px;font-weight:600;display:flex;align-items:center;justify-content:center;letter-spacing:.4px}

/* subscribe */
.mountains{left:0;top:4140px;width:1200px;height:480px;background:linear-gradient(180deg,var(--cream) 0%,#dfe2dd 25%,#9aa89a 55%,#4e6a4c 80%,#2f4a33 100%)}
.sub-box{left:283px;top:4208px;width:633px;height:58px;background:var(--white);border-radius:30px;box-shadow:0 6px 20px rgba(0,0,0,.12);display:flex;align-items:center;padding:0 6px 0 24px;font-size:14px;color:#8b9196;gap:10px}
.sub-box .send{margin-left:auto;height:46px;border-radius:24px;background:var(--teal);color:#fff;font-size:13px;font-weight:600;display:flex;align-items:center;gap:10px;padding:0 22px}

/* footer */
.footer-col{position:absolute;top:4574px;color:#fff;font-size:12.5px}
.footer-col h4{font-family:"Outfit",sans-serif;font-weight:500;font-size:16px;letter-spacing:.5px;margin-bottom:10px}
.footer-col li{list-style:none;line-height:27px}
.contact-row{display:flex;gap:10px;line-height:19px;margin-bottom:10px}
.soc{display:flex;align-items:center;gap:10px;margin-bottom:14px}
.soc span{width:28px;height:28px;border-radius:50%;border:1px solid #fff;display:inline-block}
.soc span.fill{background:var(--gold);border-color:var(--gold)}
.foot-logo{left:826px;top:4578px;width:232px;height:190px;border-radius:50%;background:var(--white);display:flex;align-items:center;justify-content:center;text-align:center;font-family:"Outfit",sans-serif;font-weight:600;color:var(--teal);font-size:24px;line-height:1.2}
.copyright{left:0;top:4828px;width:1200px;border-top:1px solid rgba(255,255,255,.2);margin:0;padding-top:14px;text-align:center;color:#fff;font-size:12px}
</style>
</head>
<body>

<header>
  <div class="abs topbar">
    <span><svg width="13" height="10" viewBox="0 0 13 10"><rect x="0.5" y="0.5" width="12" height="9" fill="none" stroke="#fff"/><path d="M.5 .5 6.5 5.5 12.5 .5" fill="none" stroke="#fff"/></svg>Email: hello@meadowlarkroaming.example</span>
    <span><svg width="12" height="12" viewBox="0 0 24 24"><path d="M6.6 10.8a15.2 15.2 0 0 0 6.6 6.6l2.2-2.2c.3-.3.7-.4 1-.2 1.1.4 2.3.6 3.6.6.6 0 1 .4 1 1V20c0 .6-.4 1-1 1A17 17 0 0 1 3 4c0-.6.4-1 1-1h3.5c.6 0 1 .4 1 1 0 1.3.2 2.5.6 3.6.1.3 0 .7-.2 1z" fill="#fff"/></svg>Phone: 555.014.2287</span>
  </div>
  <nav class="abs nav">
    <a style="left:140px">HOME</a>
    <a style="left:212px">BRIMWELL</a>
    <a style="left:300px">FAMILY TRIPS</a>
    <a style="left:421px">ROAD TRIPS</a>
    <div class="logo-badge">Meadowlark<br>Roaming</div>
    <a style="left:728px">DESTINATIONS</a>
    <a style="left:865px">ABOUT US</a>
    <a style="left:975px">CONTACT US</a>
  </nav>
</header>

<section class="abs hero">
  <div class="ph hero-photo" role="img" aria-label="Traveller in a yellow dress and sun hat on a cliff overlooking a turquoise island bay"></div>
  <svg class="abs hero-cut" width="1200" height="562" viewBox="0 0 1200 562"><path d="M0 330 C0 470 40 500 150 508 Q600 600 1050 508 C1160 500 1200 470 1200 330 L1200 562 L0 562Z" fill="#fdf9f3"/></svg>
  <div class="abs script">Adventure Starts</div>
  <h1 class="abs">Your Family<br>Adventure <em>Awaits</em></h1>
  <p class="abs">Experience unforgettable moments with Meadowlark Roaming. From Brimwell magic to Texas backroads, we craft perfect family vacations.</p>
  <div class="btn">START PLANNING NOW <span class="ring"><svg width="16" height="12" viewBox="0 0 16 12"><path d="M1 6h13M9 1l5 5-5 5" stroke="#c4924a" stroke-width="2" fill="none"/></svg></span></div>
</section>

<section>
  <div class="abs script center" style="top:740px;font-size:36px">Explore</div>
  <h2 class="abs heading center" style="top:770px;font-size:36px">Begin Your Journey.</h2>
  <p class="abs center" style="top:832px;font-size:12.5px;color:var(--muted)">Curated adventures for every family rhythm</p>

  <div class="ph card-photo" style="left:142px;top:880px;width:444px;height:326px;background:linear-gradient(160deg,#8fb6c8,#d9c8b2 60%,#9c8670)" role="img" aria-label="Family relaxing on the deck of a sailboat"></div>
  <div class="card-info" style="left:154px;top:1155px;width:420px;height:109px">
    <span class="tag" style="background:var(--gold)">Signature</span>
    <h3>Brimwell Vacations</h3><small>LAND AND SEA</small>
    <span class="go"><svg width="14" height="12" viewBox="0 0 16 12"><path d="M1 6h13M9 1l5 5-5 5" stroke="#fff" stroke-width="2" fill="none"/></svg></span>
  </div>

  <div class="ph card-photo" style="left:614px;top:880px;width:444px;height:326px;background:linear-gradient(160deg,#a8c6de,#8f9b6a 55%,#6b7a46)" role="img" aria-label="Family of five hiking along a coastal cliff"></div>
  <div class="card-info" style="left:626px;top:1155px;width:420px;height:109px">
    <span class="tag" style="background:#2e8a5a">For All Ages</span>
    <h3>Family Trips</h3><small>BONDING &amp; ADVENTURE</small>
    <span class="go"><svg width="14" height="12" viewBox="0 0 16 12"><path d="M1 6h13M9 1l5 5-5 5" stroke="#fff" stroke-width="2" fill="none"/></svg></span>
  </div>

  <div class="ph card-photo" style="left:142px;top:1290px;width:444px;height:326px;background:linear-gradient(180deg,#d8b7a0,#c27a4c 45%,#8d5c3e)" role="img" aria-label="Traveller in a hat on an open desert road with red rock buttes"></div>
  <div class="card-info" style="left:154px;top:1565px;width:420px;height:109px">
    <span class="tag" style="background:#1f6fc4">Partnered</span>
    <h3>Texas Road Trips</h3><small>PINECREST VAN RENTALS</small>
    <span class="go"><svg width="14" height="12" viewBox="0 0 16 12"><path d="M1 6h13M9 1l5 5-5 5" stroke="#fff" stroke-width="2" fill="none"/></svg></span>
  </div>

  <div class="ph card-photo" style="left:614px;top:1290px;width:444px;height:326px;background:linear-gradient(180deg,#4f8fd0,#6fb1d3 45%,#d6cdb9)" role="img" aria-label="Family walking along a sunny beach by the sea"></div>
  <div class="card-info" style="left:626px;top:1565px;width:420px;height:109px">
    <span class="tag" style="background:#5a9e2f">Beyond</span>
    <h3>Other Destinations</h3><small>BEACHES, MOUNTAINS &amp; CITIES</small>
    <span class="go"><svg width="14" height="12" viewBox="0 0 16 12"><path d="M1 6h13M9 1l5 5-5 5" stroke="#fff" stroke-width="2" fill="none"/></svg></span>
  </div>
</section>

<section>
  <div class="ph" style="left:0;top:1763px;width:1200px;height:375px;background:linear-gradient(90deg,#8a4a33 0%,#2fb3b0 30%,#43c2bf 55%,#1d7f86 80%,#6a4632 100%)" role="img" aria-label="Aerial view of a kayak on clear turquoise water between rocky cliffs"></div>
  <div class="abs banner-card">
    <div class="script">Begin Your Adventure</div>
    <h2>Best Texas<br>Getaways for Families</h2>
    <p>From Bayou Star Museum to San Antonio river walks create memories that last a lifetime.</p>
    <div class="btn">SEE FAMILY PACKAGES <span class="ring"><svg width="16" height="12" viewBox="0 0 16 12"><path d="M1 6h13M9 1l5 5-5 5" stroke="#c4924a" stroke-width="2" fill="none"/></svg></span></div>
  </div>
</section>

<section>
  <div class="abs about-text">
    <div class="script" style="font-size:34px">About</div>
    <h2 class="heading" style="font-size:34px;line-height:38px">Meadowlark Roaming<br>Travel Co.</h2>
    <div class="rule"></div>
    <p style="margin-top:18px">We assist families with planning trips, organizing itineraries, and selecting destinations that fit their needs. From Brimwell magic to Texas road adventures, let's craft memories that last a lifetime.</p>
    <p>We don't just book trips — we craft story-filled journeys. With deep local partnerships and expert knowledge of family-friendly destinations, every detail is designed to reduce stress and increase wonder. From Brimwell magic to Texas open roads, your next chapter starts here.</p>
    <div class="btn" style="margin-top:20px">READ MORE <span class="ring"><svg width="16" height="12" viewBox="0 0 16 12"><path d="M1 6h13M9 1l5 5-5 5" stroke="#c4924a" stroke-width="2" fill="none"/></svg></span></div>
  </div>
  <div class="ph" style="left:564px;top:2238px;width:242px;height:200px;border-radius:8px;background:linear-gradient(180deg,#e7d9c4,#b7a389)" role="img" aria-label="Family with bicycles reading a map on a seaside promenade"></div>
  <div class="ph" style="left:564px;top:2447px;width:242px;height:220px;border-radius:8px;background:linear-gradient(180deg,#c77a54,#5fb59a)" role="img" aria-label="Friends laughing on a boat over green water"></div>
  <div class="ph" style="left:818px;top:2285px;width:242px;height:337px;border-radius:8px;background:linear-gradient(180deg,#6aa7c4,#2f8fa4 50%,#a67c58)" role="img" aria-label="Family sitting on the bow of a boat in a tropical lagoon"></div>
</section>

<section class="abs why">
  <div class="abs script center" style="top:76px;font-size:34px">Discover</div>
  <h2 class="abs heading center" style="top:106px;font-size:36px">Why Choose Us</h2>
  <div class="abs" style="left:562px;top:156px;width:76px;height:3px;background:var(--gold)"></div>
  <p class="abs center" style="top:176px;font-size:12.5px;color:var(--muted)">Locally owned, personally crafted — we turn vacations into stories.</p>
  <svg class="abs" style="left:0;top:0" width="1200" height="676"><circle cx="600" cy="376" r="180" fill="none" stroke="#c9b79b" stroke-dasharray="4 6"/></svg>
  <div class="ph" style="left:458px;top:234px;width:284px;height:284px;border-radius:50%;background:linear-gradient(180deg,#6aa3d4,#9cc8a0 70%,#c46b3a);border:6px solid #fff" role="img" aria-label="Beach chairs under a blue sky behind the agency name"></div>
  <div class="abs" style="left:510px;top:330px;width:180px;height:92px;border-radius:14px;background:#fff;display:flex;align-items:center;justify-content:center;text-align:center;font-family:Outfit,sans-serif;font-weight:600;font-size:22px;line-height:1.15;color:var(--teal)">Meadowlark<br>Roaming</div>

  <div class="feat r" style="right:807px;top:240px;width:240px"><b>Local Expertise</b>Texas-based family, we know the best road trips &amp; hidden gems.</div>
  <div class="ico" style="left:413px;top:234px"><svg width="26" height="26" viewBox="0 0 24 24"><path d="M12 2a7 7 0 0 0-7 7c0 5 7 13 7 13s7-8 7-13a7 7 0 0 0-7-7z" fill="none" stroke="#1c5a68" stroke-width="2"/><circle cx="12" cy="9" r="2.5" fill="#c4924a"/></svg></div>

  <div class="ico" style="left:730px;top:234px"><svg width="28" height="26" viewBox="0 0 24 24"><path d="M3 15h18l-3 5H6z" fill="#1c5a68"/><rect x="7" y="9" width="10" height="5" fill="#c4924a"/><rect x="10" y="5" width="3" height="4" fill="#1c5a68"/></svg></div>
  <div class="feat" style="left:819px;top:244px;width:220px"><b>Ark &amp; Cruise Expert</b>Brimwell World,<br>Land, Cruise Lines.</div>

  <div class="feat r" style="right:858px;top:398px;width:240px"><b>Personalized Planning</b>Tailored to your family's style, budget and dreams.</div>
  <div class="ico" style="left:361px;top:382px"><svg width="24" height="26" viewBox="0 0 24 24"><rect x="5" y="4" width="14" height="18" rx="2" fill="none" stroke="#1c5a68" stroke-width="2"/><path d="M8 10h8M8 14h8M8 18h5" stroke="#c4924a" stroke-width="2"/></svg></div>

  <div class="ico" style="left:774px;top:382px"><svg width="26" height="26" viewBox="0 0 24 24"><path d="M12 3v18M12 5h7l2 3-2 3h-7M12 12H5l-2 3 2 3h7" fill="none" stroke="#1c5a68" stroke-width="2"/></svg></div>
  <div class="feat" style="left:859px;top:398px;width:230px"><b>Texas Road Trips</b>Texas-based family, we know the best road trips &amp; hidden gems.</div>

  <div class="feat r" style="right:797px;top:528px;width:240px"><b>Trusted Partners</b>Brimwell, Pinecrest Van Rentals, cruise lines &amp; more.</div>
  <div class="ico" style="left:424px;top:519px"><svg width="26" height="26" viewBox="0 0 24 24"><path d="M4 12l4-3 4 3 4-3 4 3" fill="none" stroke="#1c5a68" stroke-width="2"/><path d="M7 14l3 3 3-2 3 2" fill="none" stroke="#c4924a" stroke-width="2"/></svg></div>

  <div class="ico" style="left:707px;top:519px"><svg width="26" height="26" viewBox="0 0 24 24"><circle cx="8" cy="8" r="3" fill="#1c5a68"/><circle cx="16" cy="8" r="3" fill="#1c5a68"/><rect x="3" y="13" width="8" height="7" rx="2" fill="#1c5a68"/><rect x="13" y="13" width="8" height="7" rx="2" fill="#c4924a"/></svg></div>
  <div class="feat" style="left:792px;top:536px;width:220px"><b>100% Family Focus</b>We only serve families — that's our heartbeat.</div>
</section>

<section>
  <div class="abs script center" style="top:3500px;font-size:34px">General Inquiry</div>
  <h2 class="abs heading center" style="top:3540px;font-size:36px">Ready To Wander? Let's Talk</h2>
  <div class="abs" style="left:562px;top:3590px;width:76px;height:3px;background:var(--gold)"></div>

  <div class="field" style="left:293px;top:3625px;width:300px;height:52px"><svg width="14" height="14" viewBox="0 0 24 24"><circle cx="12" cy="8" r="4" fill="none" stroke="#9aa0a5" stroke-width="2"/><path d="M4 21c1-4 4-6 8-6s7 2 8 6" fill="none" stroke="#9aa0a5" stroke-width="2"/></svg><i></i>First Name</div>
  <div class="field" style="left:608px;top:3625px;width:300px;height:52px"><svg width="14" height="14" viewBox="0 0 24 24"><circle cx="12" cy="8" r="4" fill="none" stroke="#9aa0a5" stroke-width="2"/><path d="M4 21c1-4 4-6 8-6s7 2 8 6" fill="none" stroke="#9aa0a5" stroke-width="2"/></svg><i></i>Last Name</div>
  <div class="field" style="left:293px;top:3693px;width:300px;height:52px"><svg width="14" height="12" viewBox="0 0 13 10"><rect x="0.5" y="0.5" width="12" height="9" fill="none" stroke="#9aa0a5"/><path d="M.5 .5 6.5 5.5 12.5 .5" fill="none" stroke="#9aa0a5"/></svg><i></i>Your Email</div>
  <div class="field" style="left:608px;top:3693px;width:300px;height:52px"><svg width="14" height="14" viewBox="0 0 24 24"><path d="M6.6 10.8a15.2 15.2 0 0 0 6.6 6.6l2.2-2.2c.3-.3.7-.4 1-.2 1.1.4 2.3.6 3.6.6.6 0 1 .4 1 1V20c0 .6-.4 1-1 1A17 17 0 0 1 3 4c0-.6.4-1 1-1h3.5c.6 0 1 .4 1 1 0 1.3.2 2.5.6 3.6.1.3 0 .7-.2 1z" fill="none" stroke="#9aa0a5" stroke-width="1.6"/></svg><i></i>Phone</div>
  <div class="field" style="left:293px;top:3762px;width:615px;height:105px;align-items:flex-start;padding-top:18px"><svg width="14" height="14" viewBox="0 0 24 24"><circle cx="12" cy="12" r="9" fill="none" stroke="#9aa0a5" stroke-width="2"/></svg><i></i>Your Message</div>
  <div class="abs submit">SUBMIT NOW</div>
</section>

<section>
  <div class="ph mountains" role="img" aria-label="Misty green mountain valley"></div>
  <div class="abs script center" style="top:4030px;font-size:34px">Subscribe Now</div>
  <h2 class="abs heading center" style="top:4070px;font-size:36px;line-height:36px">Subscribe For Latest Update<br>About Travelling</h2>
  <p class="abs center" style="top:4152px;font-size:12.5px;color:var(--ink)">Latest Updates, Exclusive Content, And Special Offers? Subscribe To Our Newsletter!</p>
  <div class="abs sub-box"><svg width="16" height="12" viewBox="0 0 13 10"><rect x="0.5" y="0.5" width="12" height="9" fill="none" stroke="#8b9196"/><path d="M.5 .5 6.5 5.5 12.5 .5" fill="none" stroke="#8b9196"/></svg>Your Email<span class="send">SUBSCRIBE <svg width="16" height="12" viewBox="0 0 16 12"><path d="M1 6h13M9 1l5 5-5 5" stroke="#fff" stroke-width="2" fill="none"/></svg></span></div>
</section>

<footer>
  <svg class="abs" style="left:0;top:4520px" width="1200" height="370" viewBox="0 0 1200 370"><path d="M0 80 C0 30 30 10 90 10 Q300 0 480 40 Q600 70 720 40 Q900 0 1110 10 C1170 10 1200 30 1200 80 L1200 370 L0 370Z" fill="#0e2b31"/></svg>
  <div class="footer-col" style="left:140px"><h4>QUICK LINKS</h4><ul><li>Home</li><li>Brimwell</li><li>Family Trips</li><li>Road Trips</li><li>Destinations</li><li>About Us</li><li>Contact Us</li></ul></div>
  <div class="footer-col" style="left:331px;width:250px"><h4>CONTACT DETAILS</h4>
    <div class="contact-row"><svg width="14" height="16" viewBox="0 0 24 24"><path d="M12 2a7 7 0 0 0-7 7c0 5 7 13 7 13s7-8 7-13a7 7 0 0 0-7-7z" fill="#fff"/></svg><span>4410 Cedar Hollow Ln.<br>Pinebluff, TX 75001</span></div>
    <div class="contact-row"><svg width="14" height="14" viewBox="0 0 24 24"><path d="M6.6 10.8a15.2 15.2 0 0 0 6.6 6.6l2.2-2.2c.3-.3.7-.4 1-.2 1.1.4 2.3.6 3.6.6.6 0 1 .4 1 1V20c0 .6-.4 1-1 1A17 17 0 0 1 3 4c0-.6.4-1 1-1h3.5c.6 0 1 .4 1 1 0 1.3.2 2.5.6 3.6.1.3 0 .7-.2 1z" fill="#fff"/></svg><span>Phone<br>555.014.2287</span></div>
    <div class="contact-row"><svg width="14" height="12" viewBox="0 0 13 10"><rect x="0.5" y="0.5" width="12" height="9" fill="none" stroke="#fff"/><path d="M.5 .5 6.5 5.5 12.5 .5" fill="none" stroke="#fff"/></svg><span>Email<br>hello@meadowlarkroaming.example</span></div>
  </div>
  <div class="footer-col" style="left:617px"><h4>SOCIAL MEDIA</h4>
    <div class="soc"><span class="fill"></span>Social Page</div>
    <div class="soc"><span></span>Video Channel</div>
    <div class="soc"><span></span>Career Network</div>
    <div class="soc"><span></span>Photo Feed</div>
  </div>
  <div class="abs foot-logo">Meadowlark<br>Roaming</div>
  <p class="abs copyright">© 2026 Meadowlark Roaming Travel Co. All Rights Reserved.</p>
</footer>

</body>
</html>
```